Business Card for Coastal Tundrabridge Advisory

We need a business card for Coastal Tundrabridge Advisory. The company website address is provided below. The company logo is attached. We provide specialized permafrost services to the mining, transportation, and oil & gas industries. The card should be prepared for:
Matthias Korhonen, PhD.
Coastal Tundrabridge Advisory
PO Box 418259
Quillwater, Alaska 99642
Direct: +1-907-555-0143
Email: mkorhonen@tundrabridgeadvisory.example
Website: www.coastaltundrabridgeadvisory.example

```html
<!DOCTYPE html>
<html lang="en">
<head>
<meta charset="utf-8">
<title>Coastal Tundrabridge Advisory – Business Card</title>
<link rel="stylesheet" href="https://fonts.googleapis.com/css2?family=Exo+2:ital,wght@1,800&family=Roboto:wght@400;500&display=swap">
<style>
  :root {
    --backdrop: #ececec;
    --card-white: #ffffff;
    --band-grey: #7f7f7f;
    --band-dark: #333333;
    --card-back: #2f2f2f;
    --ink-dark: #2b2b2b;
    --ink-blue: #1f4e79;
    --ink-light: #ffffff;
    --gold: #b39c52;
  }
  html, body {
    margin: 0;
    padding: 0;
    width: 1199px;
    height: 1200px;
    overflow: hidden;
    background: var(--backdrop);
  }
  .card {
    position: absolute;
    left: 232px;
    width: 727px;
    height: 412px;
    border-radius: 28px;
    overflow: hidden;
  }
  .card--front { top: 155px; background: var(--card-white); }
  .card--back  { top: 650px; background: var(--card-back); }

  .card__bands { position: absolute; inset: 0; }
  .band--grey { fill: var(--band-grey); }
  .band--dark { fill: var(--band-dark); }

  .person {
    position: absolute;
    left: 54px;
    top: 78px;
  }
  .person__name {
    margin: 0;
    font-family: "Exo 2", sans-serif;
    font-style: italic;
    font-weight: 800;
    font-size: 27px;
    letter-spacing: 0.5px;
    color: var(--ink-dark);
    text-transform: uppercase;
    line-height: 1;
  }
  .person__title {
    margin: 6px 0 0;
    font-family: "Roboto", sans-serif;
    font-size: 14px;
    color: var(--ink-blue);
  }

  .contacts {
    position: absolute;
    left: 44px;
    top: 200px;
    margin: 0;
    padding: 0;
    list-style: none;
    font-family: "Roboto", sans-serif;
    font-weight: 500;
    font-size: 13px;
    color: var(--ink-light);
  }
  .contacts__item {
    display: flex;
    align-items: center;
    height: 23.5px;
  }
  .contacts__icon {
    width: 17px;
    height: 17px;
    margin-right: 8px;
    fill: none;
    stroke: var(--ink-light);
    stroke-width: 1.3;
  }

  .address {
    position: absolute;
    left: 270px;
    top: 362px;
    margin: 0;
    font-family: "Roboto", sans-serif;
    font-style: normal;
    font-weight: 500;
    font-size: 13px;
    line-height: 19px;
    color: var(--ink-light);
  }

  .brand {
    position: absolute;
    inset: 0;
    display: flex;
    align-items: center;
    justify-content: center;
  }
  .brand__name {
    margin: 0;
    font-family: "Roboto", sans-serif;
    font-weight: 500;
    font-size: 30px;
    letter-spacing: 5px;
    text-transform: uppercase;
    color: var(--gold);
  }
</style>
</head>
<body>

<section class="card card--front">
  <svg class="card__bands" width="727" height="412" viewBox="0 0 727 412" aria-hidden="true">
    <path class="band--grey" d="M0 174 H326 C368 174 392 190 412 222 L492 344 L492 412 H0 Z"/>
    <path class="band--dark" d="M183 412 L214 362 Q226 343 252 343 H727 V412 Z"/>
  </svg>

  <div class="person">
    <h1 class="person__name">Matthias Korhonen, PhD</h1>
    <p class="person__title">Founder &amp; Director</p>
  </div>

  <ul class="contacts">
    <li class="contacts__item">
      <svg class="contacts__icon" viewBox="0 0 18 18"><circle cx="9" cy="9" r="8"/><path d="M6 5 L7.5 5 L8.2 7 L7.2 8 Q8 10 10 10.8 L11 9.8 L13 10.5 L13 12 Q9 13 6 9.5 Q5 7 6 5 Z"/></svg>
      +1-907-555-0143
    </li>
    <li class="contacts__item">
      <svg class="contacts__icon" viewBox="0 0 18 18"><circle cx="9" cy="9" r="8"/><rect x="6.5" y="4.5" width="5" height="9" rx="1"/></svg>
      (907) 555 0143
    </li>
    <li class="contacts__item">
      <svg class="contacts__icon" viewBox="0 0 18 18"><circle cx="9" cy="9" r="8"/><rect x="5" y="6" width="8" height="6"/><path d="M5 6 L9 9.5 L13 6"/></svg>
      mkorhonen@tundrabridgeadvisory.example
    </li>
    <li class="contacts__item">
      <svg class="contacts__icon" viewBox="0 0 18 18"><circle cx="9" cy="9" r="8"/><circle cx="9" cy="9" r="4.5"/><path d="M4.5 9 H13.5 M9 4.5 Q6.5 9 9 13.5 M9 4.5 Q11.5 9 9 13.5"/></svg>
      www.coastaltundrabridgeadvisory.example
    </li>
  </ul>

  <address class="address">
    PO Box 418259<br>
    Quillwater, Alaska 99642
  </address>
</section>

<section class="card card--back">
  <div class="brand">
    <p class="brand__name">Coastal Tundrabridge Advisory</p>
  </div>
</section>

</body>
</html>
```